Casino with the 'highest winning percentage' needs a stationery design

This is for a casino in Colombo, Sri Lanka and we need a stationery design for business card, letter head and envelope.

Should be very professional, simple and elegant without fancy fonts

Reason: Not fully satisfied with the designs. Need more designs.

Business

• 1. card deck symbol 'CLUBS' in red, or black

2. name in BLOCK CAPITAL LETTERS

3. Preferred font colours are black, white or red

4. Prefer 'professional /elegant' fonts
• SHOULD NOT HAVE ANY OTHER SYMBOL EXCEPT 'CLUBS'

DO NOT PREFER ITALIC FONTS

```html
<!DOCTYPE html>
<html lang="en">
<head>
<meta charset="utf-8">
<title>Marlow's Entertainment – Business Card</title>
<link rel="stylesheet" href="https://fonts.googleapis.com/css2?family=Noto+Serif:wght@400;700&display=swap">
<style>
  :root {
    --ink: #231f20;
    --red: #d62d3f;
    --black: #0a0a0a;
    --page: #ebe8e4;
    --metal-light: #f7f7f7;
    --metal-mid: #d9d9d9;
    --metal-dark: #bdbdbd;
    --rule: #c8c8c8;
  }
  * { margin: 0; padding: 0; box-sizing: border-box; }
  html, body { width: 1193px; height: 1200px; overflow: hidden; }
  body {
    background: var(--page);
    font-family: "Noto Serif", Georgia, serif;
    color: var(--ink);
    position: relative;
  }
  .card {
    position: absolute;
    width: 921px;
    height: 525px;
    border-radius: 46px;
    overflow: hidden;
    background:
      radial-gradient(ellipse 40% 30% at 50% 50%, rgba(255,255,255,.7), rgba(255,255,255,0) 70%),
      linear-gradient(160deg, var(--metal-light) 0%, #ececec 30%, var(--metal-mid) 55%, #efefef 75%, var(--metal-dark) 100%);
    box-shadow: 0 6px 18px rgba(0,0,0,.18);
  }
  .card--front { left: 34px; top: 50px; }
  .card--back { left: 246px; top: 611px; }

  .brand-mark {
    position: absolute;
    left: 160px; top: 50px;
    width: 122px; height: 122px;
    border-radius: 50%;
    background: var(--red);
  }
  .brand-name {
    position: absolute;
    left: 338px; top: 44px;
    font-weight: 700;
    font-size: 50px;
    line-height: 66px;
    color: var(--ink);
    white-space: nowrap;
  }

  .contact { position: absolute; font-size: 24px; line-height: 37px; white-space: nowrap; }
  .contact--address { right: 496px; top: 236px; text-align: right; }
  .contact--address .phone-line { margin-bottom: 8px; }
  .contact--channels { left: 481px; top: 236px; }
  .contact-row { display: flex; align-items: center; gap: 12px; height: 37.5px; }
  .icon { width: 20px; height: 20px; flex: none; fill: var(--red); }
  .phone-line { display: flex; justify-content: flex-end; align-items: center; gap: 12px; height: 37px; }
  .divider {
    position: absolute; left: 449px; top: 226px;
    width: 1px; height: 158px; background: var(--rule);
  }
  .swoosh { position: absolute; left: 0; top: 0; width: 921px; height: 525px; }

  .suit-field {
    position: absolute; left: 217px; top: 36px; width: 452px; height: 461px;
    background: radial-gradient(ellipse at 50% 50%, rgba(190,170,172,.28), rgba(200,200,200,0) 70%);
  }
  .back-title {
    position: absolute; left: 0; right: 0; top: 176px;
    text-align: center;
    font-weight: 700;
    font-size: 68px;
    line-height: 96px;
    color: var(--ink);
  }
  .tagline {
    position: absolute; left: 0; right: 0; top: 402px;
    text-align: center;
    font-weight: 700;
    font-size: 28px;
    letter-spacing: 2.6px;
    color: var(--red);
  }
</style>
</head>
<body>

<section class="card card--front">
  <svg class="swoosh" viewBox="0 0 921 525" aria-hidden="true">
    <path d="M0 470 C180 450 420 455 640 470 C780 478 870 455 921 430 L921 525 L0 525 Z" fill="#b8b8b8"/>
    <path d="M0 433 C120 412 260 410 420 425 C560 440 700 455 800 440 C860 430 900 410 921 391 L921 430 C860 460 760 470 640 468 C460 462 300 452 160 462 C90 467 40 470 0 472 Z" fill="var(--black)"/>
    <path d="M0 488 C160 462 380 470 620 482 C780 490 870 468 921 445 L921 525 L0 525 Z" fill="var(--red)"/>
  </svg>

  <div class="brand-mark" aria-hidden="true"></div>
  <h1 class="brand-name">MARLOW'S<br>ENTERTAINMENT</h1>

  <div class="contact contact--address">
    <div class="phone-line">
      <svg class="icon" viewBox="0 0 20 20" aria-hidden="true"><circle cx="10" cy="10" r="9" fill="none" stroke="var(--red)" stroke-width="1.5"/><path d="M6.5 5.5l2 0 1 2.5-1.3 1c.6 1.3 1.5 2.2 2.8 2.8l1-1.3 2.5 1v2c-4.5.3-8.3-3.5-8-8z"/></svg>
      <span>+ 94 11 2456780</span>
    </div>
    <p>MARLOW'S LIMITED</p>
    <p>58, Lotus Garden Road</p>
    <p>Colombo 01000, Sri Lanka</p>
  </div>

  <div class="divider"></div>

  <div class="contact contact--channels">
    <div class="contact-row">
      <svg class="icon" viewBox="0 0 20 20" aria-hidden="true"><path d="M6 1h8a1 1 0 0 1 1 1v16a1 1 0 0 1-1 1H6a1 1 0 0 1-1-1V2a1 1 0 0 1 1-1zm1 2v5h6V3zm0 7v2h2v-2zm4 0v2h2v-2zm-4 3v2h2v-2zm4 0v2h2v-2z"/></svg>
      <span>+ 94 77 0000000</span>
    </div>
    <div class="contact-row">
      <svg class="icon" viewBox="0 0 20 20" aria-hidden="true"><path d="M5 3h9v4H5zM2 8h16a1 1 0 0 1 1 1v6H1V9a1 1 0 0 1 1-1zm2 8h3v2H4zm9 0h3v2h-3z"/></svg>
      <span>+ 94 11 0000000</span>
    </div>
    <div class="contact-row">
      <svg class="icon" viewBox="0 0 20 20" aria-hidden="true"><path d="M1 8l9-5 9 5v9H1zm2 1l7 5 7-5-7-4zm4-1h6v1H7zm0 2h6v1H7z"/></svg>
      <span>info@marlowscolombo.com</span>
    </div>
    <div class="contact-row">
      <svg class="icon" viewBox="0 0 20 20" aria-hidden="true"><g fill="none" stroke="var(--red)" stroke-width="1.4"><circle cx="10" cy="10" r="8.3"/><ellipse cx="10" cy="10" rx="3.6" ry="8.3"/><path d="M2 10h16M3.5 5.5h13M3.5 14.5h13"/></g></svg>
      <span>www.marlowscolombo.com</span>
    </div>
  </div>
</section>

<section class="card card--back">
  <div class="suit-field" role="img" aria-label="Faint decorative playing card suit symbols"></div>
  <h2 class="back-title">MARLOW'S<br>ENTERTAINMENT</h2>
  <p class="tagline">Highest Winning Percentage In The World</p>
</section>

</body>
</html>
```